Northvale Strategy Partners Website Design

I need a website design for my new business consulting and executive coaching firm, Northvale Strategy Partners. We provide consultative services to business C-suites as well as personal coaching to executives. I have attached the logo with color scheme I have chosen. I would like the website to reflect professionalism and continue the color scheme in the logo.

Target Market(s)

Small to medium business and their executives; middle to upper income men and women in mid- to late career looking for significance

Industry/Entity Type

Business Consultant

Number of Pages Required

4 page

Requirements
Must have
• A homepage with prominent logo and way to contact for more information; an area on the homepage with easy to read, clear text to describe what the company does; a prominent area on the homepage for a tagline; a blog page that can be updated regularly, an "about us" page with biographical information; an "about us" page; a page detailing services offered
• The web design must match the logo colors and font that I have uploaded.
Nice to have
• A lighthouse picture in the background or header
Should not have
• A lot of text area on the homepage

```html
<!DOCTYPE html>
<html lang="en">
<head>
<meta charset="utf-8">
<title>Northvale Strategy Partners</title>
<link href="https://fonts.googleapis.com/css2?family=Cormorant+Garamond:wght@500&family=Open+Sans:wght@400;600&family=Raleway:wght@500;600;800&display=swap" rel="stylesheet">
<style>
:root{
  --red:#8b0a10;
  --red-dark:#6d0408;
  --navy:#1e2c66;
  --navy-deep:#18255a;
  --btn:#1c2a5c;
  --text:#555;
  --heading:#2a2a2a;
  --logo-grey:#a5a9ad;
  --white:#fff;
}
*{margin:0;padding:0;box-sizing:border-box}
html,body{width:913px;height:1200px;overflow:hidden;background:var(--white)}
body{position:relative;font-family:"Open Sans",sans-serif;color:var(--text)}
.abs{position:absolute}
.topbar{left:0;top:0;width:913px;height:63px;background:linear-gradient(var(--red),var(--red-dark))}
.brand{left:140px;top:0;width:154px;height:115px;background:var(--white);display:flex;flex-direction:column;align-items:center;justify-content:center;z-index:3;text-align:center}
.brand-name{font-family:"Cormorant Garamond",serif;font-size:22px;line-height:1;color:var(--navy);letter-spacing:.5px}
.brand-sub{font-family:"Cormorant Garamond",serif;font-size:9px;color:var(--navy);letter-spacing:1.5px;margin-top:5px;text-transform:uppercase}
.nav{left:333px;top:29px;display:flex;font-family:"Raleway",sans-serif;font-weight:600;font-size:10.5px;color:var(--white)}
.nav span{padding:0 14px;border-left:1px solid rgba(255,255,255,.45);line-height:13px}
.nav span:first-child{border-left:0}
.hero{left:0;top:63px;width:913px;height:346px;
  background:
    radial-gradient(circle at 61px 225px,#fff6c8 0,#ffc070 12px,rgba(255,140,80,.6) 60px,rgba(255,120,90,0) 170px),
    radial-gradient(circle at 660px 55px,#ffe6d0 0,rgba(255,120,120,.75) 18px,rgba(200,70,110,.25) 70px,rgba(0,0,0,0) 130px),
    linear-gradient(180deg,rgba(0,0,0,0) 70%,rgba(20,30,50,.55) 100%),
    linear-gradient(90deg,#4a6a96 0%,#c98476 16%,#8f6a8a 36%,#59618a 52%,#6c6670 66%,#4e4a4c 82%,#3a3f4f 100%)}
.hero-title{left:140px;top:192px;font-family:"Cormorant Garamond",serif;font-weight:500;font-size:29px;line-height:31px;color:var(--white);letter-spacing:.5px}
.dots{left:139px;top:268px;display:flex;gap:2px}
.dots i{width:13px;height:13px;border-radius:50%;background:var(--white);display:block}
.dots i.on{background:#e0c21a;border:2px solid var(--white)}
.card{top:431px;width:205px;text-align:center}
.card .ph{height:132px}
.card h3{font-family:"Raleway",sans-serif;font-weight:500;font-size:13px;color:var(--heading);margin-top:14px}
.card p{font-size:8.4px;line-height:15px;margin-top:4px}
.btn{display:inline-block;margin-top:9px;width:78px;height:24px;line-height:24px;background:var(--btn);color:var(--white);font-size:8.8px;border-radius:2px}
.panel{top:702px;width:312px;height:184px;overflow:hidden}
.panel .ph{height:100%}
.panel .cap{position:absolute;left:0;bottom:0;width:100%;height:65px;padding:10px 19px;color:var(--white)}
.panel h3{font-family:"Raleway",sans-serif;font-weight:500;font-size:15px;margin-bottom:5px}
.panel p{font-size:8px;line-height:12px}
.cap.dark{background:rgba(25,25,25,.85)}
.cap.red{background:rgba(150,10,14,.85)}
.clients{left:0;top:932px;width:913px;height:67px;border-top:1px solid #e2e2e2;display:flex;align-items:center;justify-content:center;gap:38px}
.clients span{font-family:"Raleway",sans-serif;font-weight:800;font-size:18px;color:var(--logo-grey)}
.footer{left:0;top:999px;width:913px;height:159px;background:var(--navy)}
.col{top:1035px;color:var(--white)}
.col h4{font-family:"Raleway",sans-serif;font-weight:500;font-size:12px;margin-bottom:9px}
.col li{list-style:none;font-size:8.4px;line-height:16.4px;color:#d5daf0}
.divider{top:1033px;width:1px;height:80px;background:rgba(255,255,255,.15)}
.social{display:flex;gap:3px;margin-top:9px}
.social span{display:flex;align-items:center;justify-content:center;width:21px;height:21px;border:1.5px solid var(--white);border-radius:50%;font-size:5.5px;font-weight:600;color:var(--white)}
.footer-mark{left:636px;top:1088px;font-family:"Cormorant Garamond",serif;font-size:28px;color:#34457f}
.bottom{left:0;top:1158px;width:913px;height:42px;background:var(--navy-deep)}
.copy{left:142px;top:1173px;font-size:8px;color:#7d89b8}
</style>
</head>
<body>
<header>
  <div class="abs topbar"></div>
  <div class="abs brand">
    <div class="brand-name">NORTHVALE</div>
    <div class="brand-sub">Strategy Partners</div>
  </div>
  <nav class="abs nav"><span>HOME</span><span>ABOUT US</span><span>SERVICES</span><span>CLIENTS</span><span>ADVISORS</span><span>CONTACT</span></nav>
</header>

<section class="abs hero" role="img" aria-label="Stone lighthouse on a rocky shore at sunset over the sea"></section>
<h1 class="abs hero-title">BUSINESS CONSULTING &amp;<br>ADVISORY GROUP</h1>
<div class="abs dots"><i class="on"></i><i></i><i></i><i></i></div>

<section>
  <article class="abs card" style="left:138px">
    <div class="ph" role="img" aria-label="Businessman sketching a chart from problems to solution on a wall" style="background:radial-gradient(ellipse at 60% 40%,#ececea 0,#d4d4d2 55%,#a9a9a7 100%)"></div>
    <h3>WHO WE ARE</h3>
    <p>Mauris vel lacus vitae felis vestibulum volutpat E eu<br>imperdiet ac nisl Cum sociis natoque</p>
    <span class="btn">READ MORE</span>
  </article>
  <article class="abs card" style="left:354px">
    <div class="ph" role="img" aria-label="Colleagues reviewing work at a laptop in a bright office" style="background:radial-gradient(ellipse at 20% 20%,#ffffff 0,#dfe6ec 35%,rgba(223,230,236,0) 70%),linear-gradient(120deg,#cfd8df 0%,#8d949c 55%,#3c3f46 100%)"></div>
    <h3>BUSINESS CONSULTING</h3>
    <p>Mauris vel lacus vitae felis vestibulum volutpat E eu<br>imperdiet ac nisl Cum sociis natoque</p>
    <span class="btn">READ MORE</span>
  </article>
  <article class="abs card" style="left:570px">
    <div class="ph" role="img" aria-label="Hand touching a glowing digital growth chart" style="background:radial-gradient(ellipse at 62% 50%,#8ec3ee 0,#3f77ad 30%,rgba(35,65,110,0) 70%),linear-gradient(135deg,#0f1a33,#203a63 60%,#141d33)"></div>
    <h3>SERVICES PROVIDES</h3>
    <p>Mauris vel lacus vitae felis vestibulum volutpat E eu<br>imperdiet ac nisl Cum sociis natoque</p>
    <span class="btn">READ MORE</span>
  </article>
</section>

<section>
  <article class="abs panel" style="left:138px">
    <div class="ph" role="img" aria-label="Three business people smiling in a meeting" style="background:radial-gradient(ellipse at 50% 10%,#f4f7fb 0,#cfd9e4 45%,rgba(207,217,228,0) 80%),linear-gradient(180deg,#dbe3ec 0%,#8c939d 60%,#4b4f57 100%)"></div>
    <div class="cap dark"><h3>ABOUT US</h3><p>Mauris vel lacus vitae felis vestibulum volutpat imperdiet ac nisl Cum<br>sociis natoque penatibus et magnis dis parturient</p></div>
  </article>
  <article class="abs panel" style="left:463px">
    <div class="ph" role="img" aria-label="Silhouetted business people shaking hands before a city skyline" style="background:radial-gradient(circle at 58% 26%,#fff7d6 0,#e9d89a 10%,rgba(200,190,140,.5) 30%,rgba(0,0,0,0) 55%),linear-gradient(180deg,#6a8290 0%,#3f4f5a 55%,#1e2228 100%)"></div>
    <div class="cap red"><h3>OUR ADVISORS</h3><p>Mauris vel lacus vitae felis vestibulum volutpat imperdiet ac nisl Cum<br>sociis natoque penatibus et magnis dis parturient</p></div>
  </article>
</section>

<section class="abs clients">
  <span>Swiftline</span><span>Corvant</span><span>Envoyra</span><span>Qalteris</span><span>verde</span><span>Tallrow</span>
</section>

<footer>
  <div class="abs footer"></div>
  <div class="abs col" style="left:142px"><h4>COMPANY</h4><ul><li>Home</li><li>About Us</li><li>Business Consulting</li><li>Career</li></ul></div>
  <div class="abs divider" style="left:234px"></div>
  <div class="abs col" style="left:263px"><h4>SERVICES</h4><ul><li>Morbi ut mi</li><li>Nullam enim leo</li><li>egestas id</li><li>condimentum</li></ul></div>
  <div class="abs divider" style="left:353px"></div>
  <div class="abs col" style="left:379px;top:1033px"><h4>RESOURCES</h4><ul><li>Clients</li><li>Support</li><li>Term of Use</li><li>Contact Us</li></ul></div>
  <div class="abs divider" style="left:473px"></div>
  <div class="abs col" style="left:495px"><h4>FOLLOW US</h4><ul><li>Please connect with us on</li></ul>
    <div class="social" aria-label="Social links"><span>Kite</span><span>Moss</span><span>Orbit</span><span>Pier</span></div>
  </div>
  <div class="abs footer-mark">NORTHVALE</div>
  <div class="abs bottom"></div>
  <div class="abs copy">© 2015 Company Name&nbsp; All right reserved</div>
</footer>
</body>
</html>
```